Need a clean & modern homepage for an education site + opportunity for longer term work

Thanks for viewing our project. We are excited about this new website and we hope that we might build a relationship with designers as we work on this project. I provided quite a few details and requirements to help you more quickly create a design that meets our needs.
Who we are:
We are a website that discusses the importance of college accreditation and provides a directory of college programs.
What we need:
A homepage that meets the below requirements and is inspired by the examples provided
Definition of accredited:
ac·cred·it·ed [uh-kred-i-tid] adj.
1. officially recognized as meeting the essential requirements, as of academic excellence: accredited schools.
2. provided with official credentials, as by a government: an accredited diplomatic representative.
3. accepted as authoritative: an accredited theory.
Overall look and feel for the homepage:
- Clean, simple and modern
- Limited (or zero) pictures
- Utilize color blocks with text
- A trend seems to be longer vertical length homepages with lots of whitespace. I generally like this trend as long as the page is not way to tall.
Inspirations: Sites that have a similar look and feel to what I need.
http://lernvoxa.org/
http://www.campusmetrik.com/colleges/brantmoor-university/
http://quietfolding.org/
http://www.velostrahiring.com/
http://www.zunq.com/
http://sketches.bxv.com/
Items to be included on the homepage. Details below on each item.
- Top navigation
- Logo: Please leave a blank area for a logo. The logo has not been designed.
- Simple graphic/color block at the top that highlights a definition of “Accredited” – the definition should be formatted like it is being copy/pasted from a dictionary.
- Space for a video and small (50 word) written description of the video. You can use placeholder text.
- One section with 3 Paragraphs of content (each paragraph around 100 words) with a header at the top. You can use placeholder text but please create the formatting. At the end of the 3 paragraphs please have a “Read More” Note this shouldn't be 3 separate paragraphs with three read mores - it is 3 paragraphs with one read more at the end.
- An area with the header “Search Colleges by State” that has anchor text links to all 50 states.
Top navigation:
- Home
- States – with a subnav dropdown that includes all 50 US states.
- Programs – with a subnav dropdown that includes program titles (list below)
- Degrees - with a subnav dropdown that includes 5 degree levels (list below)
- Accreditation – no subnav
- Rankings – no subnav
- Resources – no subnav
Footer
- Link to about us, privacy, and a copyright www.url.com
Programs List for sub navigation
Accounting
Art
Bible
Business
Criminal Justice
Design
Education
Engineering
English
Law
LPN to RN
Management
Math
MBA
MPH
Medical Assisting
Military
Nursing
Occupational Therapy
Paralegal
Psychology
Pharmacy
RN to BSN
Radiology
Social Work
Sonography
Degrees list for sub navigation
Certificate
Associate
Bachelors
Masters
PhD
Thanks so much - looking forward to working with you!
Education

```html
<!DOCTYPE html>
<html lang="en">
<head>
<meta charset="utf-8">
<title>Accredited Colleges – Home</title>
<link rel="stylesheet" href="https://fonts.googleapis.com/css2?family=Ubuntu:ital,wght@0,300;0,400;0,500;0,700;1,300;1,400&family=Noto+Serif:wght@400;700&display=swap">
<style>
:root{
  --ink:#353a47;
  --nav-bg:#eeeeee;
  --nav-text:#7a7a7a;
  --coral:#f05a47;
  --board:#474747;
  --board-frame:#0d5aa7;
  --teal:#22b99a;
  --cyan:#23b0c9;
  --violet:#8d8dc0;
  --mist:#ececea;
  --sky:#6699cc;
  --blue-title:#29a8e0;
  --body-text:#8a8a8a;
  --white:#ffffff;
}
*{margin:0;padding:0;box-sizing:border-box}
html,body{width:1200px;height:2544px;overflow:hidden}
body{font-family:"Ubuntu",sans-serif;background:var(--white);position:relative;color:var(--body-text)}
a{color:inherit}

.site-header{height:106px;display:flex;align-items:center;justify-content:center}
.brand{font-family:"Ubuntu",sans-serif;font-weight:700;font-size:48px;color:#111;letter-spacing:1px}

.main-nav{height:49px;background:var(--nav-bg);position:relative}
.main-nav ul{list-style:none;position:absolute;left:148px;width:902px;height:49px;display:flex}
.main-nav li{font-weight:700;font-size:14px;color:var(--nav-text);text-transform:uppercase;display:flex;align-items:center;justify-content:center;letter-spacing:.5px}
.main-nav li.has-sub::after{content:"";border:5px solid transparent;border-top-color:currentColor;border-bottom:0;margin-left:10px}
.main-nav li.active{background:var(--coral);color:var(--white)}

.hero{position:absolute;top:155px;left:0;width:1200px;height:453px;background:var(--ink);overflow:hidden}
.hero-visual{position:absolute;left:123px;top:0;width:941px;height:453px;background:linear-gradient(180deg,var(--board) 0%,var(--board) 62%,var(--board-frame) 100%)}
.definition{position:absolute;left:307px;top:178px;width:640px;font-family:"Noto Serif",serif;font-size:16.5px;font-weight:700;line-height:22px;color:#f2f2f2}
.definition li{list-style-position:inside;padding-left:22px;text-indent:-22px}

.programs-menu{position:absolute;top:155px;left:148px;width:902px;height:170px;background:var(--coral);display:grid;grid-template-columns:153px 155px 153px 152px 160px;padding:24px 0 0 36px;z-index:2}
.programs-menu ul{list-style:none}
.programs-menu li{font-size:11.5px;line-height:20.8px;color:#fbe3df}
.programs-menu li.current{color:#ffd24a}

.features{position:absolute;top:608px;left:0;width:1200px;height:372px;background:var(--mist)}
.feature{position:absolute;top:39px;height:301px;color:var(--white);text-align:center;padding:26px 26px 0}
.feature.ranking{left:148px;width:289px;background:var(--teal)}
.feature.accreditation{left:456px;width:286px;background:var(--cyan)}
.feature.resources{left:761px;width:286px;background:var(--violet)}
.feature .icon{width:62px;height:62px;border-radius:50%;background:rgba(255,255,255,.85);margin:0 auto;display:flex;align-items:center;justify-content:center}
.feature h2{font-weight:300;font-size:35px;margin:6px 0 6px}
.feature p{font-size:12px;font-weight:500;line-height:16.5px}

.video-section{position:absolute;top:980px;left:0;width:1200px;height:472px;background:var(--sky);text-align:center;color:var(--white)}
.video-section h2{font-weight:300;font-size:42px;margin-top:30px;letter-spacing:.5px}
.player{position:absolute;left:367px;top:95px;width:436px;height:235px;background:var(--white)}
.player .screen{height:186px;background:linear-gradient(135deg,#6d6d6a,#a79f96 45%,#3a3a3a);position:relative}
.player .play{position:absolute;left:50%;top:50%;transform:translate(-50%,-50%)}
.player .controls{height:49px;position:relative}
.video-section p{position:absolute;left:150px;width:900px;top:345px;font-size:17px;line-height:22.5px;color:#f2f6fb}

.article{position:absolute;top:1452px;left:0;width:1200px;height:478px;padding:0 148px}
.article h2{color:var(--blue-title);font-weight:300;font-size:36px;margin-top:42px;margin-bottom:30px}
.article p{font-size:15.5px;line-height:27.5px;margin-bottom:24px}
.readmore{position:absolute;left:148px;top:411px;width:123px;height:39px;border:2px solid var(--coral);color:var(--coral);font-size:13px;display:flex;align-items:center;justify-content:center;text-transform:uppercase;text-decoration:none;letter-spacing:.3px}

.states{position:absolute;top:1930px;left:0;width:1200px;height:360px;background:var(--coral);color:var(--white)}
.states h2{position:absolute;top:30px;left:148px;width:900px;text-align:center;font-weight:300;font-size:32px;display:flex;align-items:center;gap:22px}
.states h2::before,.states h2::after{content:"";flex:1;height:1px;background:rgba(255,255,255,.7)}
.state-grid{position:absolute;left:168px;top:110px;display:grid;grid-template-columns:154px 157px 146px 155px 157px 120px;list-style:none}
.state-grid li{font-style:italic;font-size:16px;line-height:34px;font-weight:300}
.state-grid a{text-decoration:underline}

.site-footer{position:absolute;top:2290px;left:0;width:1200px;height:254px;background:var(--ink);color:var(--white);text-align:center}
.site-footer .brand{color:var(--white);font-size:37px;display:block;margin-top:28px}
.social{display:flex;justify-content:center;gap:4px;margin-top:20px}
.social span{width:32px;height:32px;display:block}
.social .s1{background:#3b5998}.social .s2{background:#2fa9e0}.social .s3{background:#d0422f}.social .s4{background:#c9202b}
.footer-links{margin-top:22px;font-size:15px}
.footer-links span{margin:0 8px}
.url{font-style:italic;font-size:14px;margin-top:14px}
</style>
</head>
<body>

<header class="site-header"><span class="brand">LOGO</span></header>

<nav class="main-nav">
  <ul>
    <li style="width:106px">Home</li>
    <li class="has-sub" style="width:124px">States</li>
    <li class="has-sub active" style="width:125px">Programs</li>
    <li class="has-sub" style="width:123px">Degrees</li>
    <li style="width:157px">Accreditation</li>
    <li style="width:127px">Rankings</li>
    <li style="width:140px">Resources</li>
  </ul>
</nav>

<section class="hero">
  <div class="hero-visual" role="img" aria-label="Illustration of a classroom chalkboard on a blue stand"></div>
  <ol class="definition">
    <li>officially recognized as meeting the essential requirements, as of academic excellence: accredited schools.</li>
    <li>provided with official credentials, as by a government: an accredited diplomatic representative.</li>
    <li>accepted as authoritative: an accredited theory.</li>
  </ol>
</section>

<div class="programs-menu">
  <ul><li class="current">Accounting</li><li>Art</li><li>Bible</li><li>Business</li><li>Criminal Justice</li><li>Design</li></ul>
  <ul><li>Education</li><li>Engineering</li><li>English</li><li>Law</li><li>LPN to RN</li><li>Management</li></ul>
  <ul><li>Math</li><li>MBA</li><li>MPH</li><li>Medical Assisting</li><li>Military</li><li>Nursing</li></ul>
  <ul><li>Occupational</li><li>Therapy</li><li>Paralegal</li><li>Psychology</li><li>Pharmacy</li><li>RN to BSN</li></ul>
  <ul><li>Radiology</li><li>Social Work</li><li>Sonography</li></ul>
</div>

<section class="features">
  <article class="feature ranking">
    <div class="icon"><svg width="30" height="30" viewBox="0 0 30 30"><path d="M8 3h14v8a7 7 0 0 1-14 0z M3 5h5v4a3 3 0 0 1-5-1z M22 5h5v3a3 3 0 0 1-5 1z M13 18h4v5h-4z M9 24h12v3H9z" fill="#22b99a"/></svg></div>
    <h2>Ranking</h2>
    <p>Lorem ipsum dolor sit amet, consectetur adipiscing elit. Fusce rutrum magna in nisi mattis, ut mollis lorem dictum. Morbi ac condimentum lacus. Phasellus dolor magna, rhoncus et interdum eget, tempor non sapien.</p>
  </article>
  <article class="feature accreditation">
    <div class="icon"><svg width="30" height="30" viewBox="0 0 30 30"><circle cx="15" cy="13" r="9" fill="#23b0c9"/><circle cx="15" cy="13" r="5" fill="#fff"/><path d="M9 20l-3 8 4-2 2 3 3-8z M21 20l3 8-4-2-2 3-3-8z" fill="#23b0c9"/></svg></div>
    <h2>Accreditation</h2>
    <p>Lorem ipsum dolor sit amet, consectetur adipiscing elit. Fusce rutrum magna in nisi mattis, ut mollis lorem dictum. Morbi ac condimentum lacus. Phasellus dolor magna, rhoncus et interdum eget, tempor non sapien.</p>
  </article>
  <article class="feature resources">
    <div class="icon"><svg width="32" height="30" viewBox="0 0 32 30"><path d="M16 5L1 12l15 7 15-7z M7 16v6c4 4 14 4 18 0v-6l-9 4z" fill="#8d8dc0"/><path d="M28 13v9" stroke="#8d8dc0" stroke-width="2"/></svg></div>
    <h2>Resources</h2>
    <p>Lorem ipsum dolor sit amet, consectetur adipiscing elit. Fusce rutrum magna in nisi mattis, ut mollis lorem dictum. Morbi ac condimentum lacus. Phasellus dolor magna, rhoncus et interdum eget, tempor non sapien.</p>
  </article>
</section>

<section class="video-section">
  <h2>WATCH OUR VIDEO</h2>
  <div class="player">
    <div class="screen" role="img" aria-label="Video still of a presenter speaking to camera">
      <svg class="play" width="70" height="70" viewBox="0 0 70 70"><circle cx="35" cy="35" r="31" fill="rgba(255,255,255,.25)" stroke="#fff" stroke-width="4"/><path d="M27 21l22 14-22 14z" fill="#fff"/></svg>
    </div>
    <div class="controls">
      <svg width="436" height="49" viewBox="0 0 436 49">
        <circle cx="28" cy="24" r="12" fill="#6f8799"/><path d="M24 18l10 6-10 6z" fill="#fff"/>
        <rect x="59" y="20" width="300" height="9" fill="#d3dde6"/>
        <rect x="59" y="20" width="138" height="9" fill="#f07c74"/>
        <g stroke="#c4ccd3" stroke-width="2.5" fill="none"><path d="M390 13l8 8M416 13l-8 8M390 36l8-8M416 36l-8-8"/><path d="M390 19v-6h6M416 19v-6h-6M390 30v6h6M416 30v6h-6"/></g>
      </svg>
    </div>
  </div>
  <p>Lorem ipsum dolor sit amet, consectetur adipiscing elit. Fusce rutrum magna in nisi mattis, ut mollis lorem dictum. Morbi ac condimentum lacus. Phasellus dolor magna, rhoncus et interdum eget, tempor non sapien. Nullam fermentum ultrices ipsum non molestie. Nunc vitae nulla ut felis ultrices mollis nec vel felis. Sed vehicula orci a orci vehicula mattis.</p>
</section>

<section class="article">
  <h2>HEADER TITLE 1</h2>
  <p>Lorem ipsum dolor sit amet, consectetur adipiscing elit. Donec accumsan nec ipsum a auctor. Nulla facilisi. Aliquam erat volutpat. Mauris suscipit diam a eros faucibus, non imperdiet urna porttitor. Nulla at faucibus libero. Donec congue tincid-<br>unt volutpat.</p>
  <p>Nulla facilisi. Nulla sit amet vehicula ante. Nunc non sapien neque. In suscipit hendrerit metus id pellentesque.<br>Proin volutpat turpis et rutrum congue. Curabitur eget ipsum volutpat, mollis est in, rutrum velit. Vivamus tellus elit, lacinia ac ullamcorper in, commodo nec nibh.</p>
  <p>Pellentesque sit amet urna nec sem pulvinar pellentesque a a lorem.<br>Proin id ultrices urna. Fusce sed nisi sed augue vehicula semper a consequat nunc. Maecenas eu feugiat erat. Integer tincid-</p>
  <a class="readmore" href="#">Readmore</a>
</section>

<section class="states">
  <h2>Search Colleges by State</h2>
  <ul class="state-grid">
    <li><a href="#">California</a></li><li><a href="#">Kentucky</a></li><li><a href="#">Louisiana</a></li><li><a href="#">California</a></li><li><a href="#">Kentucky</a></li><li><a href="#">Louisiana</a></li>
    <li><a href="#">Texas</a></li><li><a href="#">Florida</a></li><li><a href="#">Arizona</a></li><li><a href="#">Texas</a></li><li><a href="#">Florida</a></li><li><a href="#">Arizona</a></li>
    <li><a href="#">Illinois</a></li><li><a href="#">New Jersy</a></li><li><a href="#">Georgia</a></li><li><a href="#">Illinois</a></li><li><a href="#">New Jersy</a></li><li><a href="#">Georgia</a></li>
    <li><a href="#">Virginia</a></li><li><a href="#">Pennsylvania</a></li><li><a href="#">Tennessee</a></li><li><a href="#">Virginia</a></li><li><a href="#">Pennsylvania</a></li><li><a href="#">Tennessee</a></li>
    <li><a href="#">Massachusetts</a></li><li><a href="#">Alaska</a></li><li><a href="#">Colorado</a></li><li><a href="#">Massachusetts</a></li><li><a href="#">Alaska</a></li><li><a href="#">Colorado</a></li>
  </ul>
</section>

<footer class="site-footer">
  <span class="brand">LOGO</span>
  <div class="social">
    <span class="s1" role="img" aria-label="Social link"></span>
    <span class="s2" role="img" aria-label="Social link"></span>
    <span class="s3" role="img" aria-label="Social link"></span>
    <span class="s4" role="img" aria-label="Social link"></span>
  </div>
  <div class="footer-links">about us <span>|</span> privacy <span>|</span> copyright</div>
  <div class="url">www.url.com</div>
</footer>

</body>
</html>
```